wealth management firm, professional group, new model

we have a logo that works but we need a card, white background using our colors...clean look

our tag line if can be used in

Guiding Every Saver Toward Stewardship

```html
<!DOCTYPE html>
<html lang="en">
<head>
<meta charset="utf-8">
<title>Lindell Capital Group – Business Card</title>
<link rel="stylesheet" href="https://fonts.googleapis.com/css2?family=Montserrat:wght@400;500;700&display=swap">
<style>
  :root {
    --navy: #1b2a4a;
    --paper: #f6f6f5;
    --backdrop: #e3e1e1;
  }
  * { box-sizing: border-box; margin: 0; padding: 0; }
  html, body { width: 1200px; height: 1050px; overflow: hidden; }
  body {
    background: var(--backdrop);
    font-family: "Montserrat", sans-serif;
    color: var(--navy);
    display: flex;
    flex-direction: column;
    align-items: center;
    justify-content: center;
    gap: 70px;
  }
  .card {
    position: relative;
    width: 700px;
    height: 400px;
    background: var(--paper);
    box-shadow: 0 4px 14px rgba(0, 0, 0, 0.12);
  }

  /* Shared firm name */
  .firm-name {
    font-weight: 500;
    line-height: 1.1;
    white-space: nowrap;
  }

  /* Front */
  .card--front .firm-name {
    position: absolute;
    top: 130px;
    left: 0;
    right: 0;
    text-align: center;
    font-size: 44px;
  }
  .tagline-rule {
    position: absolute;
    left: 0;
    right: 0;
    bottom: 78px;
    display: flex;
    align-items: center;
    gap: 14px;
  }
  .tagline-rule::before,
  .tagline-rule::after {
    content: "";
    flex: 1;
    height: 1.5px;
    background: var(--navy);
  }
  .tagline {
    font-size: 16px;
    font-weight: 500;
    letter-spacing: 0.02em;
  }

  /* Back */
  .card--back .firm-name {
    position: absolute;
    top: 56px;
    left: 48px;
    font-size: 28px;
  }
  .person {
    position: absolute;
    top: 150px;
    left: 390px;
  }
  .person__name {
    font-size: 28px;
    font-weight: 700;
    letter-spacing: 0.01em;
  }
  .person__title {
    font-size: 15px;
    font-weight: 500;
    margin-top: 2px;
  }
  .address {
    position: absolute;
    left: 48px;
    top: 210px;
    font-size: 15px;
    font-weight: 500;
    line-height: 1.6;
    font-style: normal;
  }
  .contact {
    position: absolute;
    left: 390px;
    top: 272px;
    list-style: none;
    font-size: 15px;
    font-weight: 500;
    line-height: 1.75;
  }
  .contact li { display: flex; align-items: center; gap: 7px; }
  .contact svg { width: 12px; height: 12px; fill: var(--navy); flex: none; }
  .contact .phone { letter-spacing: 0.18em; }
</style>
</head>
<body>
  <section class="card card--front" aria-label="Business card front">
    <p class="firm-name">Lindell Capital Group</p>
    <div class="tagline-rule">
      <span class="tagline">Guiding Every Saver Toward Stewardship</span>
    </div>
  </section>

  <section class="card card--back" aria-label="Business card back">
    <p class="firm-name">Lindell Capital Group</p>
    <div class="person">
      <p class="person__name">DANIEL MARSH</p>
      <p class="person__title">Advisor</p>
    </div>
    <address class="address">
      48 Harbor Lane<br>
      Lakeview, FL 32000
    </address>
    <ul class="contact">
      <li class="phone">
        <svg viewBox="0 0 24 24" aria-hidden="true"><path d="M6.6 10.8a15.1 15.1 0 0 0 6.6 6.6l2.2-2.2a1 1 0 0 1 1-.25 11.4 11.4 0 0 0 3.6.57 1 1 0 0 1 1 1V20a1 1 0 0 1-1 1A17 17 0 0 1 3 4a1 1 0 0 1 1-1h3.5a1 1 0 0 1 1 1c0 1.25.2 2.45.57 3.57a1 1 0 0 1-.25 1z"/></svg>
        555-014-2290
      </li>
      <li>
        <svg viewBox="0 0 24 24" aria-hidden="true"><path d="M2 5h20v14H2V5zm2 2v.5l8 5 8-5V7H4z"/></svg>
        info@lindellcapital.com
      </li>
      <li>
        <svg viewBox="0 0 24 24" aria-hidden="true"><circle cx="12" cy="12" r="10" fill="none" stroke="#1b2a4a" stroke-width="2.2"/><path d="M2 12h20M12 2c3 3 3 17 0 20M12 2c-3 3-3 17 0 20" fill="none" stroke="#1b2a4a" stroke-width="1.8"/></svg>
        lindellcapital.com
      </li>
    </ul>
  </section>
</body>
</html>
```